Computer Company needs a Business card design

We need a business card design for our business. We assist people to transition to the KVS (Kestrel Vantage Scheme). The Verandal Crown Office-owned kvs™ network is a brand new telecommunications network currently being rolled out across Australia, giving access to a reliable broadband connection. Our niche market will predominantly be domestic customers in the 50+ age bracket. The assistance that we provide is everything from arranging the equipment, arranging the plan and contract term, appointment times, final testing of the network and any tweaks that need to be made. We basically PM the transition from start to finish. The business card design should be minimalist, should communicate loyalty and stability, should be easy to read and clearly explain what we do. We have asked for front and back. However, the back of the card does not have to include much information at all. It could be just a small design, or a repeat of our phone number. Up to you. The attached file only says what is required on the card. It does not specify where to arrange the text, what fonts to use, etc etc. As much as we would like to give you more info, due to our very limited design ability, we are not really able to send you any rough, or otherwise, designs of what we are after. Hopefully the above description is enough for you.

```html
<!DOCTYPE html>
<html lang="en">
<head>
<meta charset="utf-8">
<title>Harbour Connect – Business Card</title>
<link rel="stylesheet" href="https://fonts.googleapis.com/css2?family=Questrial&family=Mulish:wght@700&display=swap">
<style>
  :root {
    --backdrop: #b8b8b8;
    --brand-blue: #0584ad;
    --card-white: #f6f6f6;
    --ink-white: #ffffff;
    --ink-grey: #a3a3a3;
    --ink-dark: #4d4d4d;
  }
  * { box-sizing: border-box; margin: 0; padding: 0; }
  html, body {
    width: 1200px;
    height: 960px;
    overflow: hidden;
    background: var(--backdrop);
    font-family: "Questrial", sans-serif;
  }
  .canvas {
    position: relative;
    width: 1200px;
    height: 960px;
  }
  .card {
    position: absolute;
    left: 320px;
    width: 600px;
    height: 340px;
  }
  .card-front {
    top: 107px;
    background: var(--brand-blue);
    display: flex;
    align-items: center;
    justify-content: center;
  }
  .brand-name {
    color: var(--ink-white);
    font-family: "Questrial", sans-serif;
    font-weight: 400;
    font-size: 48px;
    letter-spacing: 0.5px;
    line-height: 1;
    transform: translateY(6px);
  }
  .card-back {
    top: 494px;
    background: var(--card-white);
  }
  .holder {
    position: absolute;
    left: 37px;
    top: 34px;
  }
  .holder-name {
    font-family: "Mulish", sans-serif;
    font-weight: 700;
    font-size: 20px;
    letter-spacing: 0.6px;
    color: var(--brand-blue);
    line-height: 1.1;
  }
  .holder-title {
    font-size: 15px;
    color: var(--ink-grey);
    letter-spacing: 0.3px;
    margin-top: 2px;
  }
  .contact-list {
    position: absolute;
    right: 40px;
    top: 249px;
    list-style: none;
    text-align: right;
  }
  .contact-item {
    display: flex;
    align-items: center;
    justify-content: flex-end;
    gap: 7px;
    font-size: 14px;
    color: var(--ink-dark);
    letter-spacing: 0.4px;
    height: 19.5px;
  }
  .contact-icon {
    width: 12px;
    height: 12px;
    flex: none;
  }
</style>
</head>
<body>
<main class="canvas">
  <section class="card card-front" aria-label="Card front">
    <h1 class="brand-name">Harbour Connect</h1>
  </section>

  <section class="card card-back" aria-label="Card back">
    <div class="holder">
      <p class="holder-name">OWEN TALLIS</p>
      <p class="holder-title">CEO/FOUNDER</p>
    </div>
    <ul class="contact-list">
      <li class="contact-item">
        <span>0491570156</span>
        <svg class="contact-icon" viewBox="0 0 12 12" aria-hidden="true">
          <path fill="#0584ad" d="M2.4 0.6 L4.2 2.8 L3.3 4.2 C3.9 5.6 5.2 7 6.8 7.8 L8.1 6.8 L10.8 8.4 L10.1 10.6 C9.6 11.4 8.4 11.5 7.2 11 C4.4 9.8 1.8 7.2 0.8 4.4 C0.4 3.2 0.7 1.7 1.4 1.1 Z"/>
        </svg>
      </li>
      <li class="contact-item">
        <span>owen@harbourconnect.com.au</span>
        <svg class="contact-icon" viewBox="0 0 12 12" aria-hidden="true">
          <rect x="0.5" y="2.2" width="11" height="7.6" fill="#0584ad"/>
          <path d="M0.8 2.6 L6 6.6 L11.2 2.6" fill="none" stroke="#f6f6f6" stroke-width="1"/>
        </svg>
      </li>
      <li class="contact-item">
        <span>www.harbourconnect.com.au</span>
        <svg class="contact-icon" viewBox="0 0 12 12" aria-hidden="true">
          <circle cx="6" cy="6" r="5.6" fill="#0584ad"/>
          <path d="M6 0.6 C3.8 3 3.8 9 6 11.4 M6 0.6 C8.2 3 8.2 9 6 11.4 M0.6 6 H11.4" fill="none" stroke="#f6f6f6" stroke-width="0.8"/>
        </svg>
      </li>
    </ul>
  </section>
</main>
</body>
</html>
```